HOME PAGE AND AND SECONDARY DESIGN FOR INTERNAL PAGES

Construction company looking for an easy to navagate professional serious greyscale website with a good clean feel simple clean menu and responsive friendly design. Our main clientele is commercial properties business owners and investors of rental properties. This website is going to be static HTML5 and would need multiple sizing files for clean fast rendering. Clean and accurate design files a must so if your experienced awesome modern greyscale designer let's get started I need this done as soon as possible.

Industry/Entity Type

construction, electrical, plumbing, commercial build outs

Number of Pages Required

2 page

Font styles to use
Sans Serif

Colors

Designer to choose only greyscale colors for use in the design.

Requirements
Must have
• Main Menu... Home, Services, Projects, About our team

```html
<!DOCTYPE html>
<html lang="en">
<head>
<meta charset="utf-8">
<title>Ironvale Builders</title>
<link href="https://fonts.googleapis.com/css2?family=Audiowide&family=Oswald:wght@300;400;500&family=Roboto:wght@400;500;700&display=swap" rel="stylesheet">
<style>
:root{
  --black:#000;
  --ink:#111;
  --panel:#2b2b2b;
  --divider:#8a8a8a;
  --band:#a9a9a9;
  --field:#e0e0e0;
  --muted:#777;
  --footer:#1c1c1c;
  --footer-text:#8c8c8c;
  --white:#fff;
}
*{box-sizing:border-box;margin:0;padding:0}
html,body{width:1200px;height:4808px;overflow:hidden}
body{position:relative;font-family:"Roboto",Arial,sans-serif;color:var(--ink);background:var(--white)}
.abs{position:absolute}
.display{font-family:"Audiowide",Arial,sans-serif;letter-spacing:3px;text-transform:uppercase}

/* header */
.site-header{top:0;left:0;width:1200px;height:84px;background:var(--black);color:var(--white)}
.nav-item{top:0;height:84px;display:flex;align-items:center;justify-content:center;font-size:13px;font-weight:500;text-transform:uppercase}
.nav-item.active{background:#bdbdbd;color:var(--ink)}
.nav-sep{top:0;width:1px;height:84px;background:#333}
.brand{left:520px;top:0;width:160px;height:84px;display:flex;align-items:center;justify-content:center;text-align:center;font-size:13px;font-weight:700;line-height:1.25;text-transform:uppercase}
.call{left:925px;top:20px;font-size:12px;font-weight:500}
.call strong{display:block;font-size:21px;font-weight:700;margin-top:2px}

/* hero */
.hero{top:84px;left:0;width:1200px;height:601px;
  background:
    radial-gradient(ellipse 420px 260px at 390px 330px,rgba(150,150,150,.55),rgba(150,150,150,0) 70%),
    radial-gradient(ellipse 360px 300px at 960px 380px,rgba(120,120,120,.5),rgba(120,120,120,0) 70%),
    radial-gradient(ellipse 260px 120px at 130px 430px,rgba(40,40,40,.9),rgba(40,40,40,0) 70%),
    linear-gradient(180deg,#a6a6a6 0%,#8c8c8c 14%,#5e5e5e 32%,#4a4a4a 50%,#2e2e2e 72%,#1c1c1c 100%)}
.hero-title{top:284px;left:0;width:1200px;text-align:center;font-size:42px;color:var(--white);letter-spacing:7px}
.hero-sub{top:336px;left:210px;width:780px;text-align:center;font-family:"Oswald",Arial,sans-serif;font-weight:300;font-size:25px;line-height:43px;color:var(--white)}
.btn{background:var(--black);color:var(--white);font-size:13px;font-weight:700;text-transform:uppercase;display:flex;align-items:center;justify-content:center}
.hero-btn{left:534px;top:435px;width:132px;height:43px}
.dots{top:619px;left:563px;display:flex;gap:7px}
.dots span{width:11px;height:11px;border-radius:50%;background:var(--white)}

/* projects */
.projects-band{top:685px;left:0;width:1200px;height:123px;background:var(--band);display:flex;align-items:center;justify-content:center;font-size:30px}
.projects-grid{top:808px;left:0;width:1200px;height:937px;background:var(--panel);display:grid;grid-template-columns:repeat(3,1fr);grid-template-rows:470px 467px;column-gap:2px}
.projects-grid::before{content:"";position:absolute;left:398px;top:12px;width:2px;height:925px;background:var(--divider)}
.projects-grid::after{content:"";position:absolute;left:799px;top:12px;width:2px;height:925px;background:var(--divider)}
.project{display:flex;flex-direction:column;color:var(--white);background:var(--panel)}
.project h3{height:80px;display:flex;align-items:center;justify-content:center;font-size:25px;font-weight:500}
.project-photo{height:306px}
.p1{background:radial-gradient(ellipse 200px 120px at 50% 65%,rgba(70,70,70,.75),rgba(70,70,70,0) 75%),linear-gradient(180deg,#cfcfcf 0%,#e6e6e6 30%,#9a9a9a 70%,#5e5e5e 100%)}
.p2{background:radial-gradient(ellipse 140px 200px at 45% 70%,rgba(60,60,60,.7),rgba(60,60,60,0) 75%),linear-gradient(180deg,#8d8d8d 0%,#e2e2e2 35%,#a8a8a8 70%,#6a6a6a 100%)}
.p3{background:radial-gradient(ellipse 200px 260px at 75% 70%,rgba(60,60,60,.75),rgba(60,60,60,0) 75%),linear-gradient(200deg,#cfcfcf 0%,#9d9d9d 45%,#7a7a7a 100%)}
.p4{background:radial-gradient(ellipse 220px 170px at 50% 70%,rgba(40,40,40,.8),rgba(40,40,40,0) 75%),linear-gradient(180deg,#f0f0f0 0%,#d4d4d4 35%,#777 75%,#4a4a4a 100%)}
.p5{background:radial-gradient(ellipse 230px 160px at 50% 78%,rgba(35,35,35,.85),rgba(35,35,35,0) 75%),linear-gradient(180deg,#5a5a5a 0%,#a9a9a9 30%,#6e6e6e 65%,#3a3a3a 100%)}
.p6{background:radial-gradient(ellipse 120px 230px at 25% 60%,rgba(60,60,60,.8),rgba(60,60,60,0) 75%),linear-gradient(180deg,#bdbdbd 0%,#e4e4e4 45%,#9c9c9c 80%,#555 100%)}
.project p{text-align:center;font-size:16px;line-height:26px;padding-top:16px}

/* clients */
.clients-title{top:1830px;left:0;width:1200px;text-align:center;font-size:30px}
.block{background:var(--black)}
.photo-a{background:radial-gradient(ellipse 260px 300px at 30% 60%,rgba(40,40,40,.85),rgba(40,40,40,0) 75%),linear-gradient(120deg,#4e4e4e 0%,#6c6c6c 40%,#b8b8b8 70%,#e6e6e6 100%)}
.photo-b{background:radial-gradient(ellipse 200px 260px at 62% 45%,rgba(50,50,50,.85),rgba(50,50,50,0) 75%),linear-gradient(180deg,#f4f4f4 0%,#d6d6d6 40%,#6a6a6a 80%,#303030 100%)}
.rule{height:2px;background:var(--ink)}
.num{width:38px;height:38px;border-radius:50%;background:var(--black);color:var(--white);font-size:15px;display:flex;align-items:center;justify-content:center}
.client-title{font-family:"Oswald",Arial,sans-serif;font-size:38px;line-height:43px;text-transform:uppercase;font-weight:400}
.client-text{font-size:14px;line-height:25.6px;color:var(--muted);text-align:justify}

/* team */
.team{top:2846px;left:0;width:1200px;height:526px;
  background:
    radial-gradient(ellipse 300px 260px at 10% 80%,rgba(190,190,190,.6),rgba(190,190,190,0) 75%),
    radial-gradient(ellipse 300px 260px at 92% 30%,rgba(195,195,195,.6),rgba(195,195,195,0) 75%),
    linear-gradient(180deg,#f4f4f4 0%,#e6e6e6 60%,#dadada 100%)}
.team-title{top:2936px;left:0;width:1200px;text-align:center;font-size:30px}
.member{top:2997px;width:315px;height:289px;background:var(--black);color:var(--white);text-align:center}
.avatar{position:absolute;left:75px;top:24px;width:165px;height:165px;border-radius:50%;border:3px solid var(--white);background:radial-gradient(circle at 50% 38%,#8a8a8a 0%,#5a5a5a 35%,#cfcfcf 60%,#e8e8e8 100%)}
.member h4{position:absolute;top:210px;width:100%;font-size:20px;font-weight:700}
.member p{position:absolute;top:238px;width:100%;font-size:13px}
.arrow{top:3133px}

/* contact */
.contact-title{top:3462px;left:0;width:1200px;text-align:center;font-size:30px}
.map{top:3517px;left:112px;width:976px;height:361px;
  background:
    radial-gradient(ellipse 220px 140px at 30% 40%,rgba(200,200,200,.9),rgba(200,200,200,0) 75%),
    radial-gradient(ellipse 260px 160px at 75% 65%,rgba(198,198,198,.9),rgba(198,198,198,0) 75%),
    linear-gradient(135deg,#dadada,#d0d0d0 50%,#d8d8d8)}
.info-icon{left:110px;width:68px;height:68px;border-radius:50%;background:var(--ink);display:flex;align-items:center;justify-content:center}
.info{left:192px;font-size:13px;font-weight:700;line-height:25px}
.info h5{font-size:20px;font-weight:700;text-transform:uppercase;line-height:30px}
.field{background:var(--field);color:#777;font-size:13px;padding:18px 18px 0}
.submit{left:599px;top:4189px;width:144px;height:51px}

/* footer */
.site-footer{top:4326px;left:0;width:1200px;height:482px;background:linear-gradient(180deg,var(--footer) 0%,var(--footer) 68%,#2c2c2c 85%,#3a3a3a 100%);color:var(--footer-text);font-size:13px}
.foot-col{top:78px}
.foot-col h6{font-size:17px;font-weight:700;color:var(--white);text-transform:uppercase;margin-bottom:16px}
.foot-col li{list-style:none;line-height:21.5px}
.foot-contact li{display:flex;gap:14px;margin-bottom:20px}
.foot-rule{top:274px;left:110px;width:980px;height:1px;background:#3a3a3a}
.copyright{top:290px;left:0;width:1200px;text-align:center}
</style>
</head>
<body>

<header class="site-header abs">
  <div class="nav-item active abs" style="left:225px;width:83px">Home</div>
  <div class="nav-item abs" style="left:318px;width:78px">About</div>
  <div class="nav-item abs" style="left:404px;width:84px">Project</div>
  <div class="brand abs">Ironvale Builders<br>LLC</div>
  <div class="nav-item abs" style="left:690px;width:90px">Services</div>
  <div class="nav-sep abs" style="left:783px"></div>
  <div class="nav-item abs" style="left:784px;width:77px">Team</div>
  <div class="nav-sep abs" style="left:863px"></div>
  <svg class="abs" style="left:888px;top:33px" width="18" height="18" viewBox="0 0 24 24" aria-hidden="true"><path fill="#fff" d="M6.6 10.8a15.1 15.1 0 0 0 6.6 6.6l2.2-2.2c.3-.3.7-.4 1-.2 1.1.4 2.3.6 3.6.6.6 0 1 .4 1 1V20c0 .6-.4 1-1 1A17 17 0 0 1 3 4c0-.6.4-1 1-1h3.5c.6 0 1 .4 1 1 0 1.3.2 2.5.6 3.6.1.3 0 .7-.2 1z"/></svg>
  <div class="call abs">Call us :<strong>512-555-0148</strong></div>
</header>

<section class="hero abs" role="img" aria-label="Black and white photo of a city skyline beside a river"></section>
<h1 class="hero-title display abs">Ironvale Builders</h1>
<p class="hero-sub abs">Lorem ipsum dolor sit amet, consectetur adipiscing elit, sed do eiusmod tempor incididunt ut labore et dolore magna aliqua.</p>
<div class="btn hero-btn abs">Get Started</div>
<div class="dots abs"><span></span><span></span><span></span><span></span></div>

<h2 class="projects-band display abs">Our Projects</h2>
<section class="projects-grid abs">
  <article class="project"><h3>PROJECT 1</h3><div class="project-photo p1" role="img" aria-label="Timber house frame under construction"></div><p>Nemo enim ipsam<br>2020</p></article>
  <article class="project"><h3>PROJECT 2</h3><div class="project-photo p2" role="img" aria-label="Towers rising with cranes"></div><p>Nemo enim ipsam<br>2020</p></article>
  <article class="project"><h3>PROJECT 3</h3><div class="project-photo p3" role="img" aria-label="High-rise under construction with crane"></div><p>Nemo enim ipsam<br>2020</p></article>
  <article class="project"><h3>PROJECT 4</h3><div class="project-photo p4" role="img" aria-label="Apartment blocks under construction"></div><p>Nemo enim ipsam<br>2020</p></article>
  <article class="project"><h3>PROJECT 5</h3><div class="project-photo p5" role="img" aria-label="Concrete frame building with two cranes"></div><p>Nemo enim ipsam<br>2020</p></article>
  <article class="project"><h3>PROJECT 6</h3><div class="project-photo p6" role="img" aria-label="Finished residential tower by the water"></div><p>Nemo enim ipsam<br>2020</p></article>
</section>

<h2 class="clients-title display abs">Our Main Client</h2>
<div class="block abs" style="left:86px;top:1913px;width:209px;height:158px"></div>
<div class="photo-a abs" style="left:112px;top:1937px;width:588px;height:403px" role="img" aria-label="Modern apartment building facade with balconies"></div>
<div class="rule abs" style="left:780px;top:1992px;width:420px"></div>
<div class="num abs" style="left:743px;top:1974px">01</div>
<h3 class="client-title abs" style="left:745px;top:2030px;width:360px">Commercial Property Business Owners</h3>
<p class="client-text abs" style="left:745px;top:2133px;width:343px">Lorem ipsum dolor sit amet, consectetur adipiscing elit, sed do eiusmod tempor incididunt ut labore et dolore magna aliqua. Ut enim ad minim veniam, quis nostrud exercitation ullamco laboris nisi ut aliquip ex ea commodo consequat. Duis aute irure dolor in reprehenderit in voluptate velit esse</p>

<div class="block abs" style="left:903px;top:2314px;width:211px;height:159px"></div>
<div class="photo-b abs" style="left:500px;top:2340px;width:588px;height:403px" role="img" aria-label="Modern residential building at dusk"></div>
<div class="rule abs" style="left:0;top:2395px;width:420px"></div>
<div class="num abs" style="left:418px;top:2377px">02</div>
<h3 class="client-title abs" style="left:110px;top:2436px;width:360px">Investors of Rental Properties</h3>
<p class="client-text abs" style="left:110px;top:2533px;width:343px">Lorem ipsum dolor sit amet, consectetur adipiscing elit, sed do eiusmod tempor incididunt ut labore et dolore magna aliqua. Ut enim ad minim veniam, quis nostrud exercitation ullamco laboris nisi ut aliquip ex ea commodo consequat. Duis aute irure dolor in reprehenderit in voluptate velit esse</p>

<section class="team abs" role="img" aria-label="Faint photo of tall buildings seen from below"></section>
<h2 class="team-title display abs">Team</h2>
<svg class="arrow abs" style="left:47px" width="18" height="22" viewBox="0 0 18 22" aria-hidden="true"><path d="M18 0v22L0 11z" fill="#111"/></svg>
<svg class="arrow abs" style="left:1134px" width="18" height="22" viewBox="0 0 18 22" aria-hidden="true"><path d="M0 0v22l18-11z" fill="#111"/></svg>
<div class="member abs" style="left:112px"><div class="avatar" role="img" aria-label="Portrait of team member"></div><h4>John Doe</h4><p>Company name</p></div>
<div class="member abs" style="left:443px"><div class="avatar" role="img" aria-label="Portrait of team member"></div><h4>John Doe</h4><p>Company name</p></div>
<div class="member abs" style="left:773px"><div class="avatar" role="img" aria-label="Portrait of team member"></div><h4>John Doe</h4><p>Company name</p></div>

<h2 class="contact-title display abs">Contact Us</h2>
<div class="map abs" role="img" aria-label="Road map of the central Texas region"></div>

<div class="info-icon abs" style="top:3911px"><svg width="22" height="28" viewBox="0 0 24 30" aria-hidden="true"><path fill="#fff" d="M12 0a11 11 0 0 0-11 11c0 8 11 19 11 19s11-11 11-19A11 11 0 0 0 12 0zm0 15a4 4 0 1 1 0-8 4 4 0 0 1 0 8z"/></svg></div>
<div class="info abs" style="top:3907px"><h5>Address :</h5>4100 Ridgeline Drive Ste 200<br>Austin, Texas 78731</div>
<div class="info-icon abs" style="top:4013px"><svg width="26" height="20" viewBox="0 0 26 20" aria-hidden="true"><path fill="#fff" d="M0 2 13 11 26 2V0H0zm0 3v15h26V5L13 14z"/></svg></div>
<div class="info abs" style="top:4017px"><h5>Email Address :</h5>info@ironvalebuilders.com</div>
<div class="info-icon abs" style="top:4118px"><svg width="24" height="24" viewBox="0 0 24 24" aria-hidden="true"><path fill="#fff" d="M6.6 10.8a15.1 15.1 0 0 0 6.6 6.6l2.2-2.2c.3-.3.7-.4 1-.2 1.1.4 2.3.6 3.6.6.6 0 1 .4 1 1V20c0 .6-.4 1-1 1A17 17 0 0 1 3 4c0-.6.4-1 1-1h3.5c.6 0 1 .4 1 1 0 1.3.2 2.5.6 3.6.1.3 0 .7-.2 1z"/></svg></div>
<div class="info abs" style="top:4121px"><h5>Phone :</h5>512-555-0148</div>

<div class="field abs" style="left:599px;top:3913px;width:235px;height:50px">Name</div>
<div class="field abs" style="left:853px;top:3913px;width:235px;height:50px">Email Address</div>
<div class="field abs" style="left:599px;top:3984px;width:487px;height:50px">Phone</div>
<div class="field abs" style="left:599px;top:4051px;width:487px;height:119px">Message</div>
<div class="btn submit abs">Submit Now</div>

<footer class="site-footer abs" role="contentinfo">
  <div class="foot-col abs" style="left:110px"><h6>Quick Links</h6><ul><li>Home</li><li>About us</li><li>Services</li><li>Testimonials</li><li>Contact</li></ul></div>
  <div class="foot-col abs" style="left:368px"><h6>FAQ</h6><ul><li>Sed ut perspiciatis unde</li><li>Omnis iste natus error sit</li><li>Voluptatem accusantium</li><li>Doloremque Sed ut perspiciatis</li><li>Unde omnis iste natus error</li></ul></div>
  <div class="foot-col foot-contact abs" style="left:659px"><h6>Contact Us</h6><ul>
    <li><span>&#9679;</span><span>4100 Ridgeline Drive Ste 200<br>Austin, Texas 78731</span></li>
    <li><span>&#9742;</span><span>512-555-0148</span></li>
    <li><span>&#9993;</span><span>info@ironvalebuilders.com</span></li></ul></div>
  <div class="foot-col abs" style="left:961px"><h6>Social Media</h6><ul><li>Facebook</li><li>Twitter</li><li>Instagram</li><li>Youtube</li><li>Linkedin</li></ul></div>
  <div class="foot-rule abs"></div>
  <p class="copyright abs">&copy; Copyrights 2023 Company name | All Rights reserved</p>
</footer>

</body>
</html>
```